Professional and Fun Business Cards for #1 Lagoon Care

We want an updated look for our existing business cards. In addition, we need to update the logos on the back side of the card to be the most current award for Tovey's Index. I have an eps of the Tovey's Index award logo but it is too big to upload here, so I can email it to the designer once selected.

Target Market(s)

Families with swimming pools

Industry/Entity Type

Business

Contact Information for Business Card

Martin Dobrev
Partner & Senior Pool Technician
Dobrev & Kin Pool Service, Inc.
2480 Larkhaven Drive, Suite 312
Roseville, CA 95874
(916) 555-0143 service
(916) 555-0187 billing
info@dobrev-kin.example
www.dobrev-kin.example

Font styles to use
Other font styles liked:
• Goudy Sans Bold

Colors
3176b5
34a7d8
34b8a4
add136

Requirements
Must have
• Dobrev & Kin logo and contact information on the front
• All other logos on the back
Nice to have
• Open to ideas...
Should not have
• Can't think of anything specific

```html
<!DOCTYPE html>
<html lang="en">
<head>
<meta charset="utf-8">
<title>Dobrev &amp; Kin Pool Service – Business Cards</title>
<link href="https://fonts.googleapis.com/css2?family=Signika:wght@400;600;700&display=swap" rel="stylesheet">
<style>
  :root {
    --teal: #3fc6b9;
    --teal-deep: #2fb3a5;
    --teal-light: #5fd6ca;
    --blue: #2d6fb5;
    --sky: #4aa9dc;
    --paper: #ffffff;
    --gold: #c9a93a;
    --seal: #b9c3d6;
    --backdrop: #ece8e1;
  }
  * { margin: 0; padding: 0; box-sizing: border-box; }
  html, body { width: 1200px; height: 885px; overflow: hidden; }
  body {
    background: var(--backdrop);
    font-family: "Signika", sans-serif;
    position: relative;
  }
  .card {
    position: absolute;
    width: 560px;
    height: 320px;
    border-radius: 4px;
    overflow: hidden;
    box-shadow: 0 10px 24px rgba(0,0,0,.18);
  }
  .card--front { left: 70px; top: 90px; background: var(--paper); }
  .card--back {
    left: 570px; top: 470px;
    background: radial-gradient(ellipse at 50% 45%, var(--teal-light), var(--teal-deep));
  }
  .card__waves { position: absolute; inset: 0; }

  .badge { position: absolute; border-radius: 50%; }
  .badge--award { left: 292px; top: 42px; width: 52px; height: 52px; background: radial-gradient(circle, #e6cf5e, var(--gold)); }
  .badge--cert { left: 372px; top: 18px; width: 66px; height: 66px; background: var(--seal); }

  .brand { position: absolute; display: flex; align-items: center; gap: 8px; color: var(--blue); font-weight: 700; }
  .brand__square { background: var(--blue); border-radius: 2px; }
  .brand__name { line-height: 1; }
  .brand__tag { display: block; font-weight: 700; letter-spacing: .32em; text-transform: uppercase; }

  .card--front .brand { left: 40px; top: 128px; }
  .card--front .brand__square { width: 30px; height: 30px; }
  .card--front .brand__name { font-size: 30px; }
  .card--front .brand__tag { font-size: 10px; margin-top: 3px; }

  .person { position: absolute; left: 40px; top: 188px; color: var(--blue); }
  .person__name { font-size: 22px; font-weight: 700; }
  .person__title { font-size: 12.5px; font-weight: 600; }

  .contacts { position: absolute; left: 370px; top: 150px; list-style: none; color: var(--paper); font-size: 13px; font-weight: 600; }
  .contacts li { display: flex; align-items: center; gap: 8px; height: 22px; }
  .contacts svg { width: 15px; height: 15px; flex: none; }

  .address { position: absolute; left: 0; right: 0; bottom: 14px; text-align: center; color: var(--paper); font-size: 13px; font-weight: 600; letter-spacing: .02em; }

  .card--back .brand { left: 50%; top: 50%; transform: translate(-50%, -50%); flex-direction: column; gap: 12px; text-align: center; }
  .mascot-area { width: 120px; height: 70px; border-radius: 6px; background: linear-gradient(135deg, #2d6fb5, #6fb6e3); }
  .card--back .brand__name { font-size: 46px; }
  .card--back .brand__tag { font-size: 14px; margin-top: 6px; }
</style>
</head>
<body>

<section class="card card--front" aria-label="Business card front">
  <svg class="card__waves" viewBox="0 0 560 320" aria-hidden="true">
    <path d="M340 0 C 300 80, 260 150, 250 230 C 245 262, 220 280, 160 290 L 0 290 L 0 320 L 560 320 L 560 0 Z" fill="var(--teal)"/>
    <path d="M325 0 C 290 70, 250 140, 240 225 C 235 258, 210 276, 150 286" fill="none" stroke="var(--paper)" stroke-width="5"/>
    <path d="M268 150 C 262 200, 250 250, 200 270 C 160 284, 80 284, 0 282 L 0 290 L 160 290 C 220 280, 250 262, 262 225 C 272 195, 272 170, 268 150 Z" fill="var(--sky)"/>
  </svg>

  <div class="badge badge--award" role="img" aria-label="Service award seal"></div>
  <div class="badge badge--cert" role="img" aria-label="Certified pool and spa operator seal"></div>

  <div class="brand">
    <span class="brand__square" aria-hidden="true"></span>
    <div>
      <span class="brand__name">Dobrev &amp; Kin</span>
      <span class="brand__tag">Pool Service</span>
    </div>
  </div>

  <div class="person">
    <p class="person__name">Martin Dobrev</p>
    <p class="person__title">Partner &amp; Senior Pool Technician</p>
  </div>

  <ul class="contacts">
    <li><svg viewBox="0 0 16 16"><rect width="16" height="16" rx="2" fill="var(--blue)"/><path d="M5 3l2 2-1 1.5c.7 1.5 1.8 2.6 3.3 3.3L10.8 9l2 2-1.3 1.6C8 12.4 3.6 8 3.4 4.5Z" fill="#fff"/></svg>(916) 555-0143</li>
    <li><svg viewBox="0 0 16 16"><rect width="16" height="16" rx="2" fill="var(--blue)"/><rect x="3.5" y="6" width="9" height="6" rx="1" fill="#fff"/><rect x="5" y="3.5" width="6" height="3" fill="#fff"/></svg>(916) 555-0187</li>
    <li><svg viewBox="0 0 16 16"><rect width="16" height="16" rx="2" fill="var(--blue)"/><rect x="3" y="4.5" width="10" height="7" fill="#fff"/><path d="M3 4.5l5 4 5-4" fill="none" stroke="var(--blue)" stroke-width="1.2"/></svg>info@dobrev-kin.example</li>
    <li><svg viewBox="0 0 16 16"><rect width="16" height="16" rx="2" fill="var(--blue)"/><circle cx="8" cy="8" r="4.5" fill="none" stroke="#fff" stroke-width="1.3"/><path d="M3.5 8h9M8 3.5c-2 2.5-2 6.5 0 9M8 3.5c2 2.5 2 6.5 0 9" fill="none" stroke="#fff" stroke-width="1"/></svg>www.dobrev-kin.example</li>
  </ul>

  <p class="address">2480 Larkhaven Drive, Suite 312 Roseville, CA 95874</p>
</section>

<section class="card card--back" aria-label="Business card back">
  <div class="brand">
    <div class="mascot-area" role="img" aria-label="Mascot illustration of a boy splashing into a pool"></div>
    <div>
      <span class="brand__name">Dobrev &amp; Kin</span>
      <span class="brand__tag">Pool Service</span>
    </div>
  </div>
</section>

</body>
</html>
```